Business Identity Stationary

Already have the logo which is in the attached files so only need the Business STationary
1) Double Sided Business Card
2) Letterhead
3) Presentation folder with business card holder on inside cover
4) WIth compliments slip
See information for business cards, letterhead and presentation folder below.

This should be a simply job using a logo we already had designed along with a little device. I suggest using the device off center and perhaps lower in the corner in an abstract way. Also the logo device could be used as a watermark for the letterhead. The designer who created the logo presented something that I think works well for a business card. The front of the double sided business card could have the name logo small for the website address and only use the Lime device on the front. Then on the back could be the name Barrow Advisory logo.

Please note that for the business card the black and lime green background do look good. Also please think of using the lime device separately in an unusual way.

It has been brought to my attention that.my budget was far to low. Hopefully this.will attract you to the project. 

The parent company of Barrow Advisory is TallHeron holdings. I have uploaded a file of the Tall Heron business card I really like. Perhaps use this business card as a guide to the type of modern and clean style I am looking for. It also works to have the Barrow Advisroy and Tall Heron similar.

Reason: Still haven't received anything exactly right.

Industry/Entity Type

Business

Font styles to use
Sans Serif

Colors
9bcb3c
000000
5c5c5c
add136
cadf82
eaf2cf
f9fbf2
1b1b1b
757575

Requirements
Must have
• 1) Double Sided Business Card
Marta Kellendorf
Director
Tel: +505 8264 3170
Email: mk@barrowadvisory-example.com
Website: www.barrowadvisory-example.com

Frederick Kellendorf
Director
Tel: +505 8264 3172
Email: fk@barrowadvisory-example.com

Lucia Brenes Otaduy
Director
Tel: 8642 1093
Email: lbo@barrowadvisory-example.com

2) Letterhead
Logo
Lime Logo Device
Website Address: www.barrowadvisory-example.com
Small print on bottom: Barrow Advisory a Tall Heron Holding Company SA. RUC J0487000239518

3) Presentation Folder
Traditional Presentation folder with inside front cover spot for the insertion of business card.

4) With Compliments slip

```html
<!DOCTYPE html>
<html lang="en">
<head>
<meta charset="utf-8">
<title>Barrow Advisory – Business Card</title>
<link rel="stylesheet" href="https://fonts.googleapis.com/css2?family=Open+Sans:wght@400;600&display=swap">
<style>
  :root {
    --stage: #1e1e1e;
    --paper: #ffffff;
    --ink: #2b2b2b;
    --lime: #9bcb3c;
    --lime-bright: #add136;
    --olive-dark: #5a7a31;
    --olive-light: #7da040;
    --card-dark: #2a2a2a;
    --card-dark-mark: #313131;
    --text-light: #f4f6ee;
  }
  * { margin: 0; padding: 0; box-sizing: border-box; }
  html, body {
    width: 1200px; height: 900px; overflow: hidden;
    background: var(--stage);
    font-family: "Open Sans", Arial, sans-serif;
  }
  .canvas { position: relative; width: 1200px; height: 900px; }

  .card {
    position: absolute; left: 355px; width: 486px; height: 270px;
    overflow: hidden;
  }
  .card--front { top: 158px; background: var(--paper); }
  .card--back  { top: 467px; background: var(--card-dark); }

  /* front */
  .brand {
    position: absolute; top: 0; left: 0; width: 100%; height: 127px;
    display: flex; align-items: center; justify-content: center; gap: 12px;
  }
  .brand__dot {
    width: 22px; height: 22px; border-radius: 50%; background: var(--lime);
  }
  .brand__name {
    font-size: 34px; font-weight: 400; color: var(--ink); letter-spacing: 0.5px;
  }
  .details {
    position: absolute; top: 127px; left: 0; width: 100%; height: 127px;
    background: linear-gradient(90deg, var(--olive-dark), var(--olive-light));
    color: var(--text-light);
  }
  .details__name {
    position: absolute; top: 16px; width: 100%; text-align: center;
    font-size: 17px; letter-spacing: 0.8px; text-transform: uppercase;
  }
  .details__role {
    position: absolute; top: 42px; width: 100%; text-align: center; font-size: 13px;
  }
  .contact {
    position: absolute; left: 28px; font-size: 11.5px;
    display: flex; align-items: center; gap: 13px;
  }
  .contact--phone { top: 78px; }
  .contact--email { top: 95px; }
  .contact svg { width: 11px; height: 11px; }
  .website {
    position: absolute; right: 32px; top: 95px; font-size: 11.5px;
  }
  .website__domain { color: var(--lime-bright); }
  .accent-strip {
    position: absolute; bottom: 0; left: 0; width: 100%; height: 16px;
    background: var(--lime);
  }

  /* back */
  .back-circle {
    position: absolute; left: 30px; top: 60px; width: 190px; height: 190px;
    border-radius: 50%; background: var(--card-dark-mark);
  }
  .back-brand {
    position: absolute; right: 22px; bottom: 52px;
    display: flex; align-items: center; gap: 12px;
  }
  .back-brand .brand__name { color: var(--text-light); font-size: 32px; }
</style>
</head>
<body>
<main class="canvas">
  <section class="card card--front">
    <div class="brand">
      <span class="brand__dot"></span>
      <span class="brand__name">Barrow Advisory</span>
    </div>
    <div class="details">
      <p class="details__name">Marta Kellendorf</p>
      <p class="details__role">Director</p>
      <p class="contact contact--phone">
        <svg viewBox="0 0 11 11" aria-hidden="true"><rect x="3" y="0.5" width="5" height="10" rx="1" fill="none" stroke="#9bcb3c" stroke-width="1.2"/><rect x="4" y="2" width="3" height="5" fill="#9bcb3c"/></svg>
        +505 8264 3170
      </p>
      <p class="contact contact--email">
        <svg viewBox="0 0 11 11" aria-hidden="true"><rect x="0.5" y="2.5" width="10" height="6.5" fill="#9bcb3c"/><path d="M0.5 2.5 L5.5 6.5 L10.5 2.5" fill="none" stroke="#5a7a31" stroke-width="1"/></svg>
        mk@barrowadvisory-example.com
      </p>
      <p class="website">www.<span class="website__domain">barrowadvisory-example</span>.com</p>
    </div>
    <div class="accent-strip"></div>
  </section>

  <section class="card card--back">
    <div class="back-circle"></div>
    <div class="back-brand">
      <span class="brand__dot"></span>
      <span class="brand__name">Barrow Advisory</span>
    </div>
  </section>
</main>
</body>
</html>
```